Church Website with Home Page and Member Sermon Library

I am in need of an updated design for our church website. This will include 4 pages (outlined below). We are a conservative, evangelical, Christian church. The site should be modern and clean, while still reflecting our conservative values. I already have a logo for our church, and I want the site to incorporate the logo, and match the logo/branding. Stock photos are allowed if needed, but I have uploaded some images of our church and would prefer those images to be used if possible. Any stock photos used should not include any people in the photos (scenery, nature, buildings, animals, etc. are fine).

The site will need 4 pages: Home, Support Us (Donate), Login, and Recording Library.

Page 1: Home
The home page should include the following sections:

- Navigation: Should include links to each section of the home page plus a "listen live" link which will take the user to a live-streaming site and a "support us" link which will take the user to a support/donate page.

- Announcements: Can be either a banner or some other design, but there needs to be some way for us to post announcements for visitors to see. I'm open for creative ideas in this section, but would like it not to take up a lot of room on the page.

- About Us: Should include address, service times (see attached document), and information about the church.

- Pastor Bio: A section that introduces our pastor and gives a short bio about our pastor. Would like this section to include a picture of our pastor. Somewhere in this section I would like to include this Bible reference: "And I will give you pastors according to mine heart, which shall feed you with knowledge and understanding. Jer 3:15 LPW"

- Articles of Faith (What We Believe): This should include several sub-sections each with a heading, body, and possibly 1 or more scripture references. I have attached a document to the brief that includes our articles of faith. Feel free to be creative with this section in how you lay these out and format them.

- Support Us: A small section that explains what kind of support someone can give and a link to a donation page. The link can say something like "Support Us" or "Donate Now".

- Contact form: A contact form that allows the visitor to send us a message. The contact form should ask for name, email, phone, and message.

- Footer: A footer that will be displayed on all pages of the site. This should include at a minimum a link to the home page (or a link to each individual section in the home page if you prefer), a link to "listen live", a link to "support us", a link to "contact us" (or you can put the contact form directly in the footer if you prefer), the address, and a "member login" link.

Page 2: Support Us
The donation page should include a form the visitor can fill out to make a donation. We will embed a third party form later. For this design, please just mock out the design with a basic form asking for name, phone, and email.

Page 3: Login
The recording library (detailed below) will require members to login with a shared numeric code before accessing the page. We need a design for a login screen. The screen should include navigation/footer just like all other pages, but the body of the login page will consist only of a form that asks the user to enter the access code and then a "login" button.

Page 4: Recording Library

The library page is a member-only page that will require a shared, numeric pass code to access. On this page, members will be able to access a filterable list of past sermons. The page by default should display most recent sermons, but should also include a search form that allows the member to filter the sermon list to find a particular sermon. The search form should allow the user to select a filter type (e.g. Speaker name, date, event, etc.) and type in a value to search. They should be able to add multiple filters and remove filters that have been added. Each sermon that is displayed in the result list should include basic information such as title, date, speaker, tags, etc. along with a download icon, and an embedded audio player where they can click a play button to stream it on-demand. Each sermon should also have clickable tags associated with it that can be used to find related sermons.
Updates

I have uploaded several images of our church. Feel free to incorporate these into your design if possible.

Target Market(s)

Church Members

Industry/Entity Type

Religion

Number of Pages Required

4 page

Font styles to use
Sans Serif

Colors

Designer to choose colors to be used in the design.

Requirements
Must have
• Must incorporate the logo (attached)
Nice to have
• Would like the design to incorporate pictures of our church (attached) instead of stock photos if possible.
Should not have
• Please avoid an overly cluttered design. Stock photos used should not include any people in the photos.

```html
<!DOCTYPE html>
<html lang="en">
<head>
<meta charset="utf-8">
<title>Grace Covenant Church</title>
<link href="https://fonts.googleapis.com/css2?family=Cinzel:wght@400;500&family=Montserrat:ital,wght@0,400;0,500;0,600;0,700;1,500&display=swap" rel="stylesheet">
<style>
:root{
  --green:#84a86a;
  --green-dark:#3d5631;
  --blue:#1bb3d6;
  --blue-soft:#2bbad6;
  --ink:#3a3a3a;
  --muted:#6b6b6b;
  --white:#ffffff;
  --foot:#f1f1ef;
}
*{box-sizing:border-box;margin:0;padding:0}
html,body{width:1200px;height:4498px;overflow:hidden}
body{font-family:"Montserrat",sans-serif;color:var(--ink);background:var(--white);position:relative}
.abs{position:absolute}
.serif{font-family:"Cinzel",serif;font-weight:400}

/* header */
.site-header{position:absolute;top:0;left:0;width:1200px;height:86px;background:var(--white)}
.brand{position:absolute;left:113px;top:22px;font-family:"Montserrat",sans-serif;font-weight:500;color:var(--blue);font-size:17px;letter-spacing:3px;line-height:20px;display:flex;align-items:center;gap:10px}
.brand .mark{width:12px;height:12px;background:var(--blue)}
.nav{position:absolute;left:360px;top:38px;display:flex;font-size:12px;font-weight:500;color:var(--green-dark)}
.nav a{color:inherit;text-decoration:none;padding:0 18px;border-left:1px solid #b9b9b9;line-height:14px}
.nav a:first-child{padding-left:0;border-left:0;color:var(--blue);position:relative}
.nav a:first-child::after{content:"";position:absolute;left:0;bottom:-12px;width:64px;height:2px;background:var(--blue)}
.pill{position:absolute;top:26px;height:37px;border-radius:19px;color:#fff;font-size:11.5px;font-weight:500;display:flex;align-items:center;justify-content:center;gap:6px}
.pill svg{width:16px;height:16px}

/* hero */
.hero{position:absolute;top:86px;left:0;width:1200px;height:559px;background:linear-gradient(180deg,#dcdcdb 0%,#d5d3d0 40%,#b99d82 62%,#8f7763 75%,#a9a39a 88%,#cfccc7 100%)}
.welcome{position:absolute;left:508px;top:48px;width:182px;height:36px;background:var(--blue);color:#fff;font-size:19px;letter-spacing:2px;display:flex;align-items:center;justify-content:center;font-family:"Cinzel",serif;z-index:2}
.hero-frame{position:absolute;left:337px;top:64px;width:526px;height:163px;border:2px solid var(--green)}
.hero-title{position:absolute;left:0;width:1200px;text-align:center;font-family:"Cinzel",serif;font-size:44px;line-height:48px;top:88px;color:var(--green)}
.hero-title span{display:block;color:var(--green-dark)}
.listen-hero{position:absolute;left:528px;top:206px;width:171px;height:42px;border-radius:21px;background:var(--green);color:#fff;font-size:15px;font-weight:500;display:flex;align-items:center;justify-content:center;gap:8px}

/* announcement */
.announce{position:absolute;top:645px;left:0;width:1200px;height:115px;background:var(--green);color:#fff;text-align:center}
.announce h2{font-size:20px;letter-spacing:2.5px;font-weight:700;margin-top:33px}
.announce p{font-size:16px;margin-top:4px}

/* about */
.about{position:absolute;top:760px;left:0;width:1200px;height:625px}
.about .frame-green{position:absolute;left:489px;top:77px;width:615px;height:459px;border:3px solid #a9c495}
.about .block-blue{position:absolute;left:108px;top:258px;width:199px;height:240px;background:var(--blue)}
.about .frame-blue{position:absolute;left:119px;top:119px;width:452px;height:377px;border:3px solid var(--blue);background:#fff}
.about .photo{position:absolute;left:120px;top:128px;width:441px;height:359px;background:linear-gradient(180deg,#c9c8c6 0%,#bdbcba 35%,#9b7c62 50%,#8d6f57 62%,#c8c6c2 72%,#d6d5d2 100%)}
.about h2{position:absolute;left:627px;top:130px;font-size:33px;color:var(--green);letter-spacing:1px}
.about .body{position:absolute;left:627px;top:195px;width:430px;font-size:12.5px;line-height:25px;color:#333}
.about .body p+p{margin-top:5px}
.about h3{position:absolute;left:627px;top:345px;color:var(--green);font-size:15px;font-weight:600}
.times{position:absolute;left:627px;top:380px;list-style:none;font-size:11.5px;font-weight:600;color:#222}
.times li{line-height:27.5px;padding-left:14px;position:relative}
.times li::before{content:"";position:absolute;left:0;top:11px;width:6px;height:6px;background:var(--green)}

/* pastor */
.pastor{position:absolute;top:1385px;left:0;width:1200px;height:608px;background:linear-gradient(180deg,#18b3d8 0%,#1fb0d2 55%,#2aa5c4 100%)}
.pastor h2{position:absolute;left:137px;top:112px;font-size:40px;color:#fff}
.rule{position:absolute;height:3px;background:#fff}
.pastor .body{position:absolute;left:139px;top:200px;width:480px;color:#fff;font-size:13.5px;font-weight:500;line-height:23px}
.pastor .body p+p{margin-top:6px}
.quote{position:absolute;left:134px;top:355px;width:476px;height:110px;border:2px solid #fff;border-radius:0 0 24px 0;color:#fff;padding:22px 40px;font-size:12.5px;line-height:21px}
.quote em{font-weight:500}
.quote b{display:block;margin-top:8px;font-weight:600;font-size:13px}
.pastor .accent{position:absolute;left:928px;top:375px;width:118px;height:116px;background:#fff}
.pastor .pframe{position:absolute;left:674px;top:102px;width:372px;height:386px;border:2px solid #fff}
.pastor .pphoto{position:absolute;left:687px;top:116px;width:347px;height:360px;background:linear-gradient(180deg,#cfc5b8 0%,#b8a48d 45%,#2b2b2e 60%,#1e1e21 100%)}

/* articles */
.faith{position:absolute;top:1993px;left:0;width:1200px;height:1050px}
.faith h2{position:absolute;left:0;width:1200px;text-align:center;top:58px;font-size:40px;color:var(--green)}
.faith .rule{background:var(--green)}
.timeline{position:absolute;width:2px;background:#c5d6b6}
.dot{position:absolute;width:13px;height:13px;border-radius:50%;background:var(--green)}
.article{position:absolute;width:420px;font-size:13px;line-height:26px;color:#444}
.article h3{font-family:"Montserrat",sans-serif;font-weight:500;font-size:21px;letter-spacing:3px;color:var(--green-dark);line-height:24px;margin-bottom:10px}
.article p+p{margin-top:8px}
.article ul{list-style:none;font-size:12px;line-height:31px;margin-top:4px}

/* support */
.support{position:absolute;top:3043px;left:0;width:1200px;height:481px;background:var(--green)}
.support .photo{position:absolute;left:0;top:0;width:583px;height:481px;background:linear-gradient(135deg,#f1efe9 0%,#e4e1da 50%,#cfcac0 100%)}
.support .panel{position:absolute;left:580px;top:0;width:620px;height:481px;background:var(--green);border-radius:0 0 0 48px}
.support h2{position:absolute;left:664px;top:98px;font-size:35px;color:#fff}
.support p{position:absolute;left:665px;top:176px;width:440px;color:#fff;font-size:17px;line-height:31px}
.donate{position:absolute;left:662px;top:310px;width:197px;height:46px;border-radius:23px;background:var(--green-dark);color:#fff;font-size:14px;font-weight:700;display:flex;align-items:center;justify-content:center}

/* contact */
.contact{position:absolute;top:3524px;left:0;width:1200px;height:553px;background:linear-gradient(180deg,#2bbcd6 0%,#33b6cf 50%,#2aa9c5 100%)}
.contact h2{position:absolute;left:0;width:1200px;text-align:center;top:78px;font-size:38px;color:#fff}
.field{position:absolute;height:53px;background:#fff;display:flex;align-items:center;gap:8px;padding-left:20px;font-size:13px;color:#555}
.field svg{width:16px;height:16px;fill:#aaa}
.send{position:absolute;left:501px;top:401px;width:194px;height:42px;border-radius:21px;background:var(--blue);color:#fff;font-size:14px;font-weight:500;display:flex;align-items:center;justify-content:center}

/* footer */
.footer{position:absolute;top:4077px;left:0;width:1200px;height:363px;background:#fff}
.footer .brand{left:142px;top:125px;font-size:18px}
.vline{position:absolute;top:90px;width:1px;height:230px;background:#d8d8d8}
.fcol{position:absolute;top:117px}
.fcol h4{font-weight:500;font-size:14px;letter-spacing:2px;color:var(--green-dark);padding-left:0}
.fcol ul{list-style:none;font-size:13px;color:#555;margin-top:16px}
.fcol ul li{line-height:30px}
.fcol p{font-size:12px;line-height:21px;color:#555;margin-top:16px}
.btn-sm{display:flex;align-items:center;justify-content:center;height:33px;border-radius:17px;color:#fff;font-size:11px;font-weight:500}
.copy{position:absolute;top:4440px;left:0;width:1200px;height:58px;background:var(--foot);text-align:center;font-size:12px;color:#666;line-height:58px}
</style>
</head>
<body>

<header class="site-header">
  <div class="brand"><span class="mark"></span>GRACE COVENANT<br>CHURCH</div>
  <nav class="nav">
    <a href="#about">ABOUT US</a>
    <a href="#pastor">PASTOR BIO</a>
    <a href="#faith">ARTICLES OF FAITH</a>
    <a href="#contact">CONTACT</a>
  </nav>
  <div class="pill" style="left:832px;width:129px;background:var(--green)">
    <svg viewBox="0 0 24 24" fill="none" stroke="#fff" stroke-width="2"><circle cx="12" cy="10" r="2"/><path d="M8 14a6 6 0 1 1 8 0M5 17a10 10 0 1 1 14 0M12 12v9"/></svg>LISTEN LIVE</div>
  <div class="pill" style="left:966px;width:128px;background:var(--blue)">
    <svg viewBox="0 0 24 24" fill="none" stroke="#fff" stroke-width="2"><path d="M4 14l6-6 4 4 6-6M4 20h16"/></svg>SUPPORT US</div>
</header>

<section class="hero" role="img" aria-label="Photo of the brick church building under an overcast sky">
  <div class="welcome">WELCOME TO</div>
  <div class="hero-frame"></div>
  <h1 class="hero-title">GRACE COVENANT<span>CHURCH</span></h1>
  <div class="listen-hero">
    <svg width="22" height="22" viewBox="0 0 24 24" fill="none" stroke="#fff" stroke-width="2"><circle cx="12" cy="10" r="2"/><path d="M8 14a6 6 0 1 1 8 0M5 17a10 10 0 1 1 14 0M12 12v9"/></svg>LISTEN LIVE</div>
</section>

<section class="announce">
  <h2>ANNOUNCEMENT HEADLINE</h2>
  <p>Ut enim ad minim veniam quis nostrud exercitation Allamco laboris nisi ut aliquip ex ea</p>
</section>

<section class="about" id="about">
  <div class="frame-green"></div>
  <div class="block-blue"></div>
  <div class="frame-blue"></div>
  <div class="photo" role="img" aria-label="Photo of the church building and parking lot"></div>
  <h2 class="serif">ABOUT OUR CHURCH</h2>
  <div class="body">
    <p>Lorem ipsum dolor sit amet, consectetur adipiscing elit, sed do eiusmod tempor incididunt ut labore et dolore magna aliqua. Ut enim ad minim veniam quis nostrud exercitation</p>
    <p>Allamco laboris nisi ut aliquip ex ea commodo consequat. Duis aute irure dolor in reprehenderit in voluptate velit.</p>
  </div>
  <h3>SERVICE TIMING:</h3>
  <ul class="times">
    <li>Wednesday Night Service: 7:30 PM</li>
    <li>Sunday School: 10:00 AM</li>
    <li>Sunday Morning Service: 11:00 AM</li>
    <li>Sunday Night Service: 5:30 PM</li>
  </ul>
</section>

<section class="pastor" id="pastor">
  <h2 class="serif">OUR PASTOR</h2>
  <div class="rule" style="left:140px;top:170px;width:96px"></div>
  <div class="body">
    <p>Lorem ipsum dolor sit amet, consectetur adipiscing elit, sed do eiusmod tempor incididunt ut labore et dolore magna aliqua. Ut enim ad minim veniam, quis nostrud exercitation</p>
    <p>Allamco laboris nisi ut aliquip ex ea commodo consequat. Duis aute irure dolor in reprehenderit in voluptate velit esse</p>
  </div>
  <div class="quote"><em>“And I will give you pastors according to mine heart, which shall feed you with knowledge and understanding”</em><b>Jer 3:15 LPW</b></div>
  <div class="accent"></div>
  <div class="pframe"></div>
  <div class="pphoto" role="img" aria-label="Portrait photo of the pastor holding a Bible"></div>
</section>

<section class="faith" id="faith">
  <h2 class="serif">ARTICLES OF FAITH</h2>
  <div class="rule" style="left:560px;top:113px;width:90px;height:2px"></div>

  <div class="timeline" style="left:121px;top:220px;height:600px"></div>
  <div class="timeline" style="left:624px;top:220px;height:600px"></div>
  <div class="dot" style="left:115px;top:214px"></div>
  <div class="dot" style="left:115px;top:438px"></div>
  <div class="dot" style="left:115px;top:811px"></div>
  <div class="dot" style="left:618px;top:214px"></div>
  <div class="dot" style="left:618px;top:438px"></div>
  <div class="dot" style="left:618px;top:628px"></div>
  <div class="dot" style="left:618px;top:818px"></div>

  <div class="article" style="left:152px;top:214px">
    <h3>THE GOD HEAD.</h3>
    <p>We believe in the God head bodily, known as the Divine Trinity. This body consist of God the father, Jesus Christ, his only begotten son and the redeemer of the world, and of the Holy Ghost, The third person of the Divine Trinity.</p>
  </div>
  <div class="article" style="left:152px;top:436px;font-size:12px">
    <h3>FULL SALVATION</h3>
    <p>We believe that Salvation is received only when a person comes to the realization that he or she is lost and separated from God and becomes full of godly sorrow, confessing their sins and true repentance, believing in the shed blood of the Lord Jesus Christ as the only sacrifice for sins. Through the blood of Christ we have:</p>
    <ul>
      <li>(1) remission of sins, Matthew 26:28 Heb 9:22</li>
      <li>(2) Sanctification. Hebrews 13:12</li>
      <li>(3) redemption. Revelations 5:9</li>
      <li>(4) cleansing. 1 John 1:7 Rev. 1:5</li>
      <li>(5). Justification. Romans 5:9</li>
    </ul>
  </div>
  <div class="article" style="left:154px;top:809px">
    <h3>SANCTIFICATION</h3>
    <p>“Sanctify them through thy truth thy word is truth St John 17:17. For this is the will of God even your sanctification”</p>
    <p>We believe in a set apart life, separate from the world to Christ 2 Cor 6:17-18</p>
  </div>

  <div class="article" style="left:653px;top:214px;width:440px">
    <h3>BAPTISM OF THE HOLY GHOST</h3>
    <p>We believe in the baptism of the Holy Ghost as it is taught in the Bible and promised by our Lord Jesus Christ, with speaking in tongues as the Spirit gives utterance as the initial evidence. Acts 2:4 we believe that the gift of the Holy Ghost is for all believers as the Lord promised. Acts 2:17-1</p>
  </div>
  <div class="article" style="left:653px;top:436px;width:440px">
    <h3>DIVINE HEALING</h3>
    <p>We believe Divine Healing to be included in the atonement of Jesus Christ our Lord, And believe that it is still for us today. 1 Peter 2:24 Luke 9:1-2 Mark 16-18 James 5:15</p>
  </div>
  <div class="article" style="left:653px;top:626px;width:440px">
    <h3>SECOND COMING OF CHRIST</h3>
    <p>We believe in the second coming of Jesus Christ. Matthew 24:44 Luke 12:40</p>
  </div>
  <div class="article" style="left:653px;top:809px;width:440px">
    <h3>ETERNITY</h3>
    <p>We believe in Literal Eternity. Eternal Life for the believer and eternal death for those without Christ. Revelations 21:1-27</p>
  </div>
</section>

<section class="support">
  <div class="photo" role="img" aria-label="Photo of a hand placing a folded dollar bill into an offering slot"></div>
  <div class="panel"></div>
  <h2 class="serif">SUPPORT US</h2>
  <div class="rule" style="left:666px;top:152px;width:90px"></div>
  <p>Lorem ipsum dolor sit amet, consectetur adipiscing elit, sed do eiusmod tempor incididunt ut labore et dolore magna aliqua. Ut enim ad minim veniam, quis nostrud exercitation</p>
  <div class="donate">DONATE NOW</div>
</section>

<section class="contact" id="contact" role="img" aria-label="Tinted photo of the church building behind the contact form">
  <h2 class="serif">CONTACT US</h2>
  <div class="rule" style="left:556px;top:127px;width:90px;height:2px"></div>
  <div class="field" style="left:201px;top:146px;width:390px">
    <svg viewBox="0 0 24 24"><circle cx="12" cy="7" r="5"/><path d="M2 23c0-6 4-9 10-9s10 3 10 9z"/></svg>First Name</div>
  <div class="field" style="left:601px;top:146px;width:390px">
    <svg viewBox="0 0 24 24"><circle cx="12" cy="7" r="5"/><path d="M2 23c0-6 4-9 10-9s10 3 10 9z"/></svg>Last Name</div>
  <div class="field" style="left:201px;top:215px;width:390px">
    <svg viewBox="0 0 24 24"><path d="M6 2l4 4-2 3c1 3 4 6 7 7l3-2 4 4-3 4C10 22 2 14 2 5z"/></svg>Email address</div>
  <div class="field" style="left:601px;top:215px;width:390px">
    <svg viewBox="0 0 24 24"><path d="M2 5h20v14H2zM2 5l10 8 10-8" fill="none" stroke="#aaa" stroke-width="2"/></svg>Phone</div>
  <div class="field" style="left:201px;top:277px;width:790px;height:98px;align-items:flex-start;padding-top:16px">Message</div>
  <div class="send">SEND MESSAGE</div>
</section>

<footer class="footer">
  <div class="brand"><span class="mark"></span>GRACE COVENANT<br>CHURCH</div>
  <div class="vline" style="left:402px"></div>
  <div class="vline" style="left:601px"></div>
  <div class="vline" style="left:856px"></div>
  <div class="fcol" style="left:427px">
    <h4>NAVIGATION</h4>
    <ul><li>About Us</li><li>Paster Bio</li><li>Article of Faith</li><li>Listen Live</li><li>Contact Us</li></ul>
  </div>
  <div class="fcol" style="left:624px;width:210px">
    <h4>DONATION</h4>
    <p>Lorem ipsum dolor sit amet, consectetur adipiscing elit, sed do eiusmod tempor inci</p>
    <div class="btn-sm" style="width:134px;margin-top:16px;background:var(--green)">DONATE NOW</div>
  </div>
  <div class="fcol" style="left:885px;width:200px">
    <h4>CONTACT US</h4>
    <div style="display:flex;gap:12px;margin-top:12px">
      <svg width="30" height="30" viewBox="0 0 24 24"><circle cx="12" cy="12" r="12" fill="var(--green)"/><path d="M12 5a4.5 4.5 0 0 0-4.5 4.5C7.5 13 12 19 12 19s4.5-6 4.5-9.5A4.5 4.5 0 0 0 12 5z" fill="#fff"/><circle cx="12" cy="9.5" r="1.6" fill="var(--green)"/></svg>
      <p style="margin-top:0;font-size:11.5px;line-height:16px">210 Meadow Lane, Suite 4, Fairhaven, OH 45001 USA</p>
    </div>
    <div class="btn-sm" style="width:134px;margin-top:20px;background:var(--blue)">MEMBER LOGIN</div>
  </div>
</footer>

<div class="copy">© 2023 <u>Grace Covenant Church</u>. All Rights Reserved</div>

</body>
</html>
```